Logo, Web and Mobile Designs for enterprise social media platform

All the details are in the attached document, please start reading the scope document first which explains what is this project about and the details about the needed deliverables, after that please read the UI_Requirements document which will detail what is expected regarding the coded web version since this is a coded contest, it is very important that you meet the UI requirements or suggest something else but we will need to agree first before working on the coded version

Good Luck

Target Market(s)

Enterprise Social Media

Industry/Entity Type

Media

Coding

Coded - Design and coding required

Number of Pages Required

5+ page

Font styles to use
Sans Serif

Requirements
Must have
• All the must haves are listed in the scope document so please check before you start

```html
<!DOCTYPE html>
<html lang="en">
<head>
<meta charset="utf-8">
<title>Teamora</title>
<link rel="stylesheet" href="https://fonts.googleapis.com/css2?family=Ubuntu:wght@400&family=PT+Sans:wght@400&family=Open+Sans:wght@300&display=swap">
<style>
  :root {
    --white: #ffffff;
    --ink: #1c1c1c;
    --orange: #f07f1f;
    --orange-dark: #d8661a;
    --black-btn: #141414;
    --night: #0e1a3a;
    --night-deep: #070c1f;
    --violet: #5a3a86;
    --green-glow: #1f6b3b;
    --link: #555555;
    --muted: #8a8a8a;
    --dot: #6a6e78;
  }
  * { margin: 0; padding: 0; box-sizing: border-box; }
  html, body { width: 1200px; height: 783px; overflow: hidden; background: var(--white); }
  body { position: relative; font-family: "PT Sans", sans-serif; color: var(--ink); }

  .site-header { position: absolute; left: 0; top: 0; width: 1200px; height: 98px; background: var(--white); }
  .brand { position: absolute; left: 110px; top: 28px; display: flex; align-items: center; gap: 12px; }
  .brand-mark { width: 47px; height: 47px; border-radius: 50%; background: var(--orange); }
  .brand-name { font-family: "Ubuntu", sans-serif; font-size: 25px; color: var(--ink); letter-spacing: 0.3px; }
  .header-actions { position: absolute; top: 28px; left: 831px; display: flex; gap: 19px; }
  .btn { width: 119px; height: 45px; border-radius: 3px; display: flex; align-items: center; justify-content: center;
         font-family: "Ubuntu", sans-serif; font-size: 14px; letter-spacing: 0.4px; text-transform: uppercase; }
  .btn-signup { background: linear-gradient(var(--orange), var(--orange-dark)); color: var(--white); }
  .btn-login { background: var(--black-btn); color: var(--white); }

  .hero { position: absolute; left: 0; top: 98px; width: 1200px; height: 589px; overflow: hidden; }
  .hero-backdrop { position: absolute; inset: 0;
    background:
      radial-gradient(ellipse 520px 180px at 640px 360px, rgba(120,80,180,0.55), transparent 70%),
      radial-gradient(ellipse 300px 120px at 760px 330px, rgba(40,140,70,0.35), transparent 70%),
      radial-gradient(ellipse 700px 160px at 600px 520px, rgba(110,70,160,0.45), transparent 70%),
      linear-gradient(180deg, var(--night-deep) 0%, var(--night) 55%, #241a40 75%, #1a1430 100%); }
  .hero-content { position: absolute; left: 110px; top: 326px; width: 560px; color: var(--white); }
  .hero-title { font-family: "Open Sans", sans-serif; font-weight: 300; font-size: 64px; line-height: 1; letter-spacing: 1px; }
  .hero-text { margin-top: 18px; font-size: 12px; line-height: 20.5px; }
  .slider-dots { display: flex; gap: 5px; margin-top: 16px; }
  .slider-dots span { width: 10px; height: 10px; border-radius: 50%; background: var(--dot); }
  .slider-dots .is-active { background: var(--orange); }

  .site-footer { position: absolute; left: 0; top: 687px; width: 1200px; height: 96px; background: var(--white); }
  .footer-nav a { position: absolute; top: 26px; font-size: 12px; color: var(--link); text-decoration: none; }
  .copyright { position: absolute; left: 111px; top: 57px; font-size: 12px; color: var(--muted); }
</style>
</head>
<body>
  <header class="site-header">
    <div class="brand">
      <span class="brand-mark"></span>
      <span class="brand-name">Teamora</span>
    </div>
    <nav class="header-actions">
      <a class="btn btn-signup">Sign up</a>
      <a class="btn btn-login">Login</a>
    </nav>
  </header>

  <section class="hero">
    <div class="hero-backdrop" role="img" aria-label="Night photograph of an illuminated arch bridge over a river with city lights"></div>
    <div class="hero-content">
      <h1 class="hero-title">TEAMORA</h1>
      <p class="hero-text">Lorem ipsum dolor sit amet, consectetur adipiscing elit. Praesent ut arcu sed dolor luctus maximus sed at nunc. Duis rutrum quam eget scelerisque sollicitudin.</p>
      <div class="slider-dots"><span></span><span></span><span class="is-active"></span><span></span></div>
    </div>
  </section>

  <footer class="site-footer">
    <nav class="footer-nav">
      <a style="left:111px">About</a>
      <a style="left:174px">Privacy</a>
      <a style="left:267px">Cookies</a>
      <a style="left:359px">Terms</a>
      <a style="left:452px">Help</a>
      <a style="left:513px">Settings</a>
      <a style="left:606px">Activity Log</a>
    </nav>
    <p class="copyright">Teamora © 2015</p>
  </footer>
</body>
</html>
```